Dog Snacks brand needs a new packaging design

Dear Designers,

We are looking for a packaging expert to design our new line of Dog Snacks which contain a relaxing hemp extract (CBD).

Our company is already selling various relaxing cat & dog products , and we would like this new design to reflect the same "style & feeling" as our current products (see attached instructions).

Technical aspects:
- The packaging is a Stand Up Pouch (12x18.5x7cm - see attached instructions).
- Please follow technical guidelines from printer (see attached instructions).
- The packaging will contain 120g of high-quality, semi-moist dog snacks.
- We will be designing 3 differents variations for 3 different flavours: Chicken, Beef & Liver.
- The packaging will be printed with a matt finish.

Design aspects:
- The design should be compatible with our brand identity (i.e. fluffly, pure, relaxing, positive, clean & natural).
- Soft/rounded shapes are preferred.
- Please use our brand's colors (#3BA384, White & Black).
- Please use our company logo (see attached instructions).
- The design also needs to convey a strong sense of professionalism as we are an animal "healthcare" brand.
- If you want to include a dog picture, we would prefer you to use a picture of our official brand ambassador (see attached instructions).
- We have attached a number of packaging examples which we like a lot. (see attached instructions). Please only use those as general inspiration.
- Only original work (no plagiarism will be accepted).

Please don't hesitate to send us a message if you have any questions about the brand, the product or the design requirements.

We look forward to seeing your designs & working on this together !

Thanks & regards,
Tobias

Target Market(s)

Dog owners

Industry/Entity Type

Pet Care

Font styles to use
Sans Serif

Requirements
Must have
• Please see project description.
Nice to have
Should not have

```html
<!DOCTYPE html>
<html lang="en">
<head>
<meta charset="utf-8">
<title>VerdaBites CBD Treats – Simply Chicken</title>
<link href="https://fonts.googleapis.com/css2?family=Raleway:wght@500;600;700;800&family=Yellowtail&family=Playfair+Display:wght@700;800&display=swap" rel="stylesheet">
<style>
  :root {
    --stage-a: #62c9cf;
    --stage-b: #2fb8c3;
    --brand-green: #3ba384;
    --top-teal: #62c7b8;
    --mint: #86cfbd;
    --mint-pale: #b5e2d6;
    --cloud: #eef6f3;
    --ink-teal: #1d6a64;
    --ink-dark: #174f4b;
    --white: #ffffff;
    --fur-a: #f1efec;
    --fur-b: #d9d2cc;
    --biscuit-a: #c79a6e;
    --biscuit-b: #8f6a48;
  }
  * { box-sizing: border-box; margin: 0; padding: 0; }
  html, body { width: 1200px; height: 793px; overflow: hidden; }
  body {
    background: linear-gradient(100deg, var(--stage-a), var(--stage-b));
    font-family: "Raleway", sans-serif;
    position: relative;
  }
  .pack-front {
    position: absolute;
    left: 347px; top: 46px;
    width: 507px; height: 700px;
    box-shadow: 0 14px 30px rgba(0, 60, 70, .22);
  }
  .pack-shapes { position: absolute; inset: 0; }
  .pack-front > div, .pack-front > p { position: absolute; }

  .brand-name {
    left: 0; right: 0; top: 42px;
    text-align: center;
    font-weight: 700; font-size: 25px; letter-spacing: 1px;
    color: var(--white);
  }
  .info-row {
    left: 26px; right: 26px; top: 94px;
    display: flex; justify-content: space-between;
    font-size: 11.5px; font-weight: 600; letter-spacing: .6px;
    color: var(--white);
  }
  .info-row strong { font-weight: 800; font-size: 13px; }
  .benefits {
    left: 0; right: 0; top: 154px;
    text-align: center;
    font-size: 14px; font-weight: 700; letter-spacing: 2.2px;
    color: var(--ink-teal);
  }
  .product-name {
    left: 0; right: 0; top: 176px;
    text-align: center;
    font-weight: 800; font-size: 62px; letter-spacing: -2.5px;
    color: var(--ink-teal);
  }
  .product-name sup { font-size: 10px; font-weight: 700; letter-spacing: 0; vertical-align: 40px; }
  .cbd-pill {
    left: 354px; top: 248px;
    width: 58px; height: 26px; border-radius: 13px;
    background: var(--ink-teal); border: 2px solid var(--white);
    color: var(--white);
    font-size: 17px; font-weight: 600;
    display: flex; align-items: center; justify-content: center;
  }
  .treats-word {
    left: 296px; top: 240px;
    font-family: "Yellowtail", cursive;
    font-size: 76px; line-height: 1;
    color: var(--brand-green);
    transform: rotate(-8deg);
  }
  .flavour {
    left: 265px; top: 318px;
    font-family: "Playfair Display", serif;
    font-weight: 800; line-height: 1;
  }
  .flavour .simply { display: block; font-size: 34px; color: var(--white); }
  .flavour .chicken { display: block; font-size: 38px; color: var(--ink-dark); margin-left: 22px; }

  .thc-badge {
    left: 409px; top: 404px;
    width: 84px; height: 84px; border-radius: 50%;
    background: var(--ink-teal);
    outline: 3px dotted var(--ink-teal); outline-offset: 4px;
    color: var(--mint-pale);
    text-align: center; line-height: .95;
    display: flex; flex-direction: column; justify-content: center;
  }
  .thc-badge .no { font-size: 26px; font-weight: 600; }
  .thc-badge .thc { font-size: 19px; font-weight: 600; }
  .thc-badge .pct { font-size: 10px; font-weight: 600; }

  .tagline {
    left: 0; right: 0; top: 664px;
    text-align: center;
    font-size: 15px; font-weight: 600;
    color: var(--ink-dark);
  }
</style>
</head>
<body>
  <main class="pack-front">
    <svg class="pack-shapes" viewBox="0 0 507 700" width="507" height="700">
      <defs>
        <linearGradient id="fur" x1="0" y1="0" x2="1" y2="1">
          <stop offset="0" stop-color="var(--fur-a)"/>
          <stop offset="1" stop-color="var(--fur-b)"/>
        </linearGradient>
        <radialGradient id="biscuits" cx=".45" cy=".45" r=".6">
          <stop offset="0" stop-color="var(--biscuit-a)"/>
          <stop offset="1" stop-color="var(--biscuit-b)"/>
        </radialGradient>
      </defs>
      <!-- body -->
      <rect width="507" height="700" fill="var(--mint)"/>
      <!-- top band -->
      <rect width="507" height="112" fill="var(--top-teal)"/>
      <!-- info stripe -->
      <rect y="91" width="507" height="22" fill="var(--brand-green)"/>
      <!-- lower pale sweep -->
      <path d="M0 420 C120 390 260 360 507 330 L507 630 L0 630 Z" fill="var(--mint-pale)" opacity=".6"/>
      <path d="M240 470 C270 420 330 400 420 402 L430 440 C350 440 300 450 260 480 Z" fill="var(--brand-green)"/>
      <!-- white cloud with centre notch -->
      <path d="M0 113 L228 113 C240 118 248 128 253 141 C258 128 266 118 278 113 L507 113 L507 210
               C480 270 400 306 300 308 C190 310 90 260 0 236 Z" fill="var(--cloud)"/>
      <path d="M0 236 C90 262 190 312 300 310 L300 318 C190 320 90 276 0 252 Z" fill="var(--brand-green)" opacity=".45"/>
      <!-- bottom band with notch -->
      <path d="M0 631 L228 631 C240 626 248 616 253 603 C258 616 266 626 278 631 L507 631 L507 653 L0 653 Z" fill="var(--brand-green)"/>
      <rect y="653" width="507" height="47" fill="var(--top-teal)"/>
      <!-- photo areas -->
      <path d="M0 300 C40 276 150 270 235 300 C250 360 250 520 248 631 L0 631 Z" fill="url(#fur)" role="img" aria-label="Photo of a white wrinkled puppy looking down"/>
      <ellipse cx="344" cy="537" rx="112" ry="96" fill="url(#biscuits)" role="img" aria-label="Photo of bone-shaped chicken dog treats"/>
      <path d="M382 565 C420 548 452 560 458 600 C470 640 500 690 498 700 L367 700 C380 660 372 600 382 565 Z" fill="url(#fur)" role="img" aria-label="Photo of a small sitting puppy"/>
    </svg>

    <p class="brand-name">VERDALO</p>
    <div class="info-row"><span>NET WEIGHT 120G</span><span>CBD <strong>250</strong>mg</span></div>
    <p class="benefits">SUPPORT • CALM • EASE</p>
    <p class="product-name">VerdaBites<sup>TM</sup></p>
    <p class="treats-word">Treats</p>
    <div class="cbd-pill">CBD</div>
    <p class="flavour"><span class="simply">Simply</span><span class="chicken">Chicken</span></p>
    <div class="thc-badge"><span class="no">NO</span><span class="thc">THC</span><span class="pct">0% THC</span></div>
    <p class="tagline">“Recommended By Veterinarians”</p>
  </main>
</body>
</html>
```